Industry / Entity Type

Financial consultancy / advisers

Current site is: http://www.brightmoor-counsel.com

Looking for a complete overhaul of this site, we are after a clean modern look. Will require the ability to easily add, update and remove content, hence the WordPress design.
Example:
Add case studies
Industry documentation (downloadable brochures / flyers and such)

What we like from our current site is the colour the fonts and the logo (the city of London) we would like to have other city outlines (NYC and Tokyo, Hong Kong, Singapore).

The site will be used by our potential clients to get in contact and re-view the case studies, if possible would like to have a client login area where they can download our documents like NDA’s etc and T&C’s.

Task Outline

Create a Web Design (Coded - Design and coding required)
Designer must provide full implementation/coding depending on the platform chosen by the client (i.e. WordPress theme, HTML/CSS, bootstrap etc.)

Task Description

I need a full website built that must work on desktop and mobile. I can provide the London city skyline and the font file, which we have used. Some stock industrial photos will be required.

Requirements:

*Splash page
*What We Do
*How We do it
*Who Are We? To have the same information and links as the current site
*Why use us?
*Clients: To have the same information and links as the current site
*Partners: To have the same information and links as the current site
*Contact:

Target Market(s)

Financial institutions trading Equities, Futures, Options, Forex and Fixed Income.
Regulators, Exchanges, ECN’s
Buy side firms and Sell side firms

Industry/Entity Type

Financial

Coding

Coded - Design and coding required

Number of Pages Required

5+ page

Font styles to use
Sans Serif

Colors
f04a50

Requirements
Must have
• Splash page
• What We Do
• How We do it
• Who Are We? To have the same information and links as the current site
• Why use us?
• Clients: To have the same information and links as the current site
• Partners: To have the same information and links as the current site
• Contact:

```html
<!DOCTYPE html>
<html lang="en">
<head>
<meta charset="utf-8">
<title>Brightmoor Counsel</title>
<link href="https://fonts.googleapis.com/css2?family=Cinzel:wght@600;700&family=Montserrat:wght@300;400;600&family=Open+Sans:wght@400;600;700&display=swap" rel="stylesheet">
<style>
:root{
  --red:#f04a50;
  --dark:#1e1e1e;
  --bar:#3a3a3a;
  --ink:#333;
  --text:#777;
  --light:#e2e2e2;
  --mid:#a5a5a5;
  --clients-bg:#ebebeb;
  --white:#fff;
}
*{margin:0;padding:0;box-sizing:border-box}
html,body{width:1200px;height:2917px;overflow:hidden}
body{position:relative;background:var(--white);font-family:"Open Sans",Arial,sans-serif;color:var(--ink)}
a{color:inherit;text-decoration:none}
.abs{position:absolute}

/* header */
.site-header{left:0;top:0;width:1200px;height:140px;background:var(--white)}
.brand{left:0;width:1200px;top:0;height:140px;display:flex;flex-direction:column;align-items:center;justify-content:center}
.brand-skyline{width:220px;height:56px;background:linear-gradient(180deg,#fff,#d8d8d8);border-bottom:2px solid #555}
.brand-name{font-family:"Cinzel",serif;font-weight:600;font-size:22px;letter-spacing:3px;color:#222;margin-top:8px}

/* nav */
.main-nav{left:0;top:140px;width:1200px;height:55px;background:linear-gradient(180deg,#2c2c2c,#141414);display:flex;padding-left:128px}
.main-nav a{height:55px;line-height:55px;padding:0 16px;font-size:17px;color:var(--white)}
.main-nav a.active{background:var(--red);width:102px;text-align:center;padding:0}

/* hero */
.hero{left:0;top:195px;width:1200px;height:517px;background:radial-gradient(ellipse at 50% 45%,#0f4d6e 0%,#0a2540 40%,#05101c 80%)}
.hero-title{left:0;width:1200px;top:150px;text-align:center;font-family:"Cinzel",serif;font-weight:700;color:var(--white);line-height:1}
.hero-title .l1{display:block;font-size:48px;letter-spacing:1px}
.hero-title .l2{display:block;font-size:40px;margin-top:8px}
.hero-btn{left:533px;top:272px;width:152px;height:41px;border:1px solid var(--white);color:var(--white);font-size:16px;text-align:center;line-height:39px}
.dots{left:0;width:1200px;top:479px;display:flex;justify-content:center;gap:8px}
.dots span{width:14px;height:14px;border-radius:50%;background:var(--white)}
.dots span.on{background:transparent;border:2px solid var(--white)}

/* features */
.features{left:0;top:712px;width:1200px;height:368px;overflow:hidden;background:linear-gradient(90deg,var(--red) 50%,var(--light) 50%)}
.features-circle{left:417px;top:0;width:368px;height:368px;border-radius:50%;background:var(--mid)}
.feature{top:0;width:300px;height:368px;text-align:center;color:var(--white)}
.feature svg{position:absolute;left:124px;top:78px}
.feature h3{position:absolute;top:160px;width:300px;font-family:"Montserrat",sans-serif;font-weight:600;font-size:21px}
.feature p{position:absolute;top:194px;left:40px;width:220px;font-size:12.5px;line-height:21px}
.feature .more{position:absolute;top:272px;left:110px;width:80px;font-size:13px;padding-bottom:4px;border-bottom:1px solid currentColor}
.feature.dark{color:#555}
.f1{left:128px}.f2{left:451px}.f3{left:784px}

/* who */
.who-title{left:138px;top:1168px;font-family:"Montserrat",sans-serif;font-weight:600;font-size:24px;letter-spacing:1px;color:#222}
.who-text{left:138px;top:1222px;width:470px;font-size:15.5px;line-height:29px;color:var(--text)}
.who-text p+p{margin-top:12px}
.btn-outline{left:134px;top:1400px;width:152px;height:41px;border:2px solid var(--red);color:var(--red);font-size:16px;text-align:center;line-height:37px}
.who-art{left:642px;top:1167px;width:438px;height:273px;border-radius:8px;background:radial-gradient(circle at 50% 50%,#dfeef6 0%,#eef5f8 50%,#fff 80%)}

/* clients */
.clients{left:0;top:1552px;width:1200px;height:393px;background:var(--clients-bg);border-bottom:1px solid #d0d0d0}
.clients h2{position:absolute;top:56px;width:1200px;text-align:center;font-family:"Montserrat",sans-serif;font-weight:600;font-size:25px;color:#555}
.client{position:absolute;width:180px;margin-left:-90px;text-align:center;font-weight:700;font-size:21px;color:#8e8e8e;display:flex;align-items:center;justify-content:center;gap:8px}
.client i{width:14px;height:14px;background:#8e8e8e;display:inline-block}
.r1{top:146px}.r2{top:243px}
.c1{left:204px}.c2{left:410px}.c3{left:613px}.c4{left:801px}.c5{left:1017px}

/* news */
.news-title{left:117px;top:2010px;font-family:"Montserrat",sans-serif;font-weight:600;font-size:26px;color:var(--red)}
.news-skyline{left:190px;top:2363px;width:820px;height:171px;background:linear-gradient(180deg,rgba(255,255,255,0),#f2f2f2)}
.card{top:2056px;width:300px}
.card-img{width:300px;height:177px}
.card h4{margin-top:26px;font-size:15px;font-weight:600;color:var(--red)}
.card p{margin-top:10px;font-size:11.5px;line-height:20px;color:var(--text)}
.card .more{display:block;margin-top:10px;font-size:12px;color:#555}
.n1{left:111px}.n2{left:445px}.n3{left:780px}
.img1{background:linear-gradient(135deg,#c9dced,#4f7ea8 60%,#2a4c72)}
.img2{background:linear-gradient(135deg,#5a4636,#a58b70 55%,#d9d2c8)}
.img3{background:linear-gradient(135deg,#444,#9a8c78 50%,#e4e0d8)}

/* footer */
.site-footer{left:0;top:2534px;width:1200px;height:312px;background:var(--dark);color:#ddd}
.footer-brand{left:126px;top:63px;width:331px;text-align:center}
.footer-brand .brand-skyline{width:210px;height:54px;margin:0 auto;background:linear-gradient(180deg,#1e1e1e,#3c3c3c);border-bottom:2px solid #ccc}
.footer-brand .brand-name{color:#fff;font-size:18px;letter-spacing:3px}
.fcol{top:70px}
.fcol h5{font-family:"Montserrat",sans-serif;font-weight:400;font-size:19px;color:#fff;margin-bottom:8px}
.fcol a,.fcol span{display:block;font-size:15px;line-height:28.5px;color:#ccc}
.col1{left:496px}.col2{left:667px}.col3{left:850px}
.social{left:836px;top:2774px;display:flex;gap:7px}
.social span{width:37px;height:37px;border-radius:50%;background:#444}
.bottom-bar{left:0;top:2846px;width:1200px;height:71px;background:var(--bar);text-align:center;line-height:71px;font-size:12px;color:#aaa}
</style>
</head>
<body>

<header class="site-header abs">
  <a class="brand abs" href="http://www.brightmoor-counsel.com">
    <span class="brand-skyline" role="img" aria-label="Brightmoor Counsel city skyline outline"></span>
    <span class="brand-name">Brightmoor Counsel</span>
  </a>
</header>

<nav class="main-nav abs">
  <a class="active" href="#">Home</a>
  <a href="#">What we do</a>
  <a href="#">How we do it</a>
  <a href="#">Who are we</a>
  <a href="#">Why use us</a>
  <a href="#">Clients</a>
  <a href="#">Partners</a>
  <a href="#">Contact</a>
</nav>

<section class="hero abs" role="img" aria-label="Glowing blue financial market chart background">
  <h1 class="hero-title abs"><span class="l1">Brightmoor Counsel</span><span class="l2">Services</span></h1>
  <a class="hero-btn abs" href="#">Read More</a>
  <div class="dots abs"><span class="on"></span><span></span><span></span><span></span></div>
</section>

<section class="features abs">
  <div class="features-circle abs"></div>
  <div class="feature f1 abs">
    <svg width="52" height="50" viewBox="0 0 52 50" fill="none" stroke="#fff" stroke-width="2"><rect x="6" y="4" width="40" height="30" rx="2"/><path d="M2 40h48l-3 5H5z"/><path d="M12 27l9-9 6 5 11-12"/><path d="M32 11h6v6"/></svg>
    <h3>HOW WE DO IT</h3>
    <p>blandit sed nulla In ullamcorper est eget tempor cursus neque mi con-sectetuer mi a ultricies</p>
    <a class="more" href="#">Click here →</a>
  </div>
  <div class="feature f2 abs">
    <svg width="52" height="52" viewBox="0 0 52 52" fill="none" stroke="#fff" stroke-width="2"><circle cx="26" cy="26" r="24"/><circle cx="26" cy="26" r="14"/><circle cx="26" cy="26" r="6"/><path d="M26 10v6M26 36v6M10 26h6M36 26h6M15 15l4 4M33 33l4 4M37 15l-4 4M15 37l4-4"/></svg>
    <h3>WHY USE US</h3>
    <p>blandit sed nulla In ullamcorper est eget tempor cursus neque mi con-sectetuer mi a ultricies</p>
    <a class="more" href="#">Click here →</a>
  </div>
  <div class="feature f3 dark abs">
    <svg width="52" height="56" viewBox="0 0 52 56" fill="none" stroke="#555" stroke-width="2"><path d="M18 40c0-8-10-12-10-22a14 14 0 0 1 28 0c0 10-10 14-10 22z"/><path d="M18 45h8M18 50h8"/><circle cx="22" cy="18" r="4"/><path d="M26 18h20M40 18v5M45 18v5"/></svg>
    <h3>WHAT WE DO</h3>
    <p>blandit sed nulla In ullamcorper est eget tempor cursus neque mi con-sectetuer mi a ultricies</p>
    <a class="more" href="#">Click here →</a>
  </div>
</section>

<section class="who">
  <h2 class="who-title abs">WHO WE ARE</h2>
  <div class="who-text abs">
    <p>Praesent sit amet est In dictum dolor eu dictum porttitor enim felis viverra mi eget luctus massa</p>
    <p>In imperdiet sit amet sem Aliquam nec erat at purus cursus interdum Vestibulum ligula augue bibendum accumsan ves-tibulum ut commodo a mi Morbi ornare gravida elit Integer</p>
  </div>
  <a class="btn-outline abs" href="#">Read More</a>
  <div class="who-art abs" role="img" aria-label="Flat illustration of charts, graphs and analytics tools"></div>
</section>

<section class="clients abs">
  <h2>OUR CLIENTS</h2>
  <div class="client r1 c1"><i></i>Tilevale</div>
  <div class="client r1 c2">Northwater</div>
  <div class="client r1 c3">Corvane</div>
  <div class="client r1 c4">Unionwide</div>
  <div class="client r1 c5">Harbrook</div>
  <div class="client r2 c1">Thermwell</div>
  <div class="client r2 c2">Civic Health</div>
  <div class="client r2 c3">Petwise</div>
  <div class="client r2 c4">Kelmora</div>
  <div class="client r2 c5">Stonecrest</div>
</section>

<section class="news">
  <div class="news-skyline abs" role="img" aria-label="Faint outline of world city skylines"></div>
  <h2 class="news-title abs">LATEST NEWS</h2>
  <article class="card n1 abs">
    <div class="card-img img1" role="img" aria-label="Hands using a tablet showing financial charts"></div>
    <h4>Alandit sed nulla In ullamcorper</h4>
    <p>mi a ultricies massa est sed nisl Class aptent taciti sociosqu ad litora torquent per conubia nostra per inceptos hymenaeos Proin nulla</p>
    <a class="more" href="#">READ MORE</a>
  </article>
  <article class="card n2 abs">
    <div class="card-img img2" role="img" aria-label="Business meeting around a desk with documents"></div>
    <h4>Est eget tempor cursus neque</h4>
    <p>mi a ultricies massa est sed nisl Class aptent taciti sociosqu ad litora torquent per conubia nostra per inceptos hymenaeos Proin nulla</p>
    <a class="more" href="#">READ MORE</a>
  </article>
  <article class="card n3 abs">
    <div class="card-img img3" role="img" aria-label="Office desk with laptop and paperwork from above"></div>
    <h4>Proin nulla arcu nonumm</h4>
    <p>mi a ultricies massa est sed nisl Class aptent taciti sociosqu ad litora torquent per conubia nostra per inceptos hymenaeos Proin nulla</p>
    <a class="more" href="#">READ MORE</a>
  </article>
</section>

<footer class="site-footer abs">
  <div class="footer-brand abs">
    <div class="brand-skyline" role="img" aria-label="Brightmoor Counsel city skyline outline"></div>
    <div class="brand-name">Brightmoor Counsel</div>
  </div>
  <div class="fcol col1 abs">
    <h5>COMPANY</h5>
    <a href="#">Home</a><a href="#">What we do</a><a href="#">How we do it</a><a href="#">Contact</a>
  </div>
  <div class="fcol col2 abs">
    <h5>RESOURCES</h5>
    <a href="#">Who are we</a><a href="#">Why use us</a><a href="#">Clients</a><a href="#">Partners</a>
  </div>
  <div class="fcol col3 abs">
    <h5>CONTACT INFO</h5>
    <span>418 Linden Park Road Suite B12</span>
    <span>Ashford, PA 19310</span>
    <span>(555) 014-2780</span>
    <span>info@brightmoor-counsel.com</span>
  </div>
</footer>
<div class="social abs">
  <span aria-label="Social network one"></span>
  <span aria-label="Social network two"></span>
  <span aria-label="Social network three"></span>
  <span aria-label="Social network four"></span>
</div>

<div class="bottom-bar abs">© 2017 Brightmoor Counsel&nbsp; All right reserved&nbsp; Term of Use</div>

</body>
</html>
```